Homeowners Insurance Provider Website

We are selling homeowners insurance policy / tenants Policy/Flood Insurance in USA in few states and planning expand nationally.

Our target audience are two folds: Customers (Buy policies) and Insurance Agents who wants to work with us to sell our policies to customers. But website should focus 80% on customers and 20% on agents. So, more customer focused user experience. Please note that there is no direct buy option for customers. They always go through insurance agents.

Customer focused, educational that makes buyer journey easy. We don’t want to come off as trying sell something as there is no direct sales involved from website.

Target Market(s)

Homeowners in USA and Insurance agent who sells these insurance.

Industry/Entity Type

Insurance

Number of Pages Required

4 page

Font styles to use
Other font styles liked:
• Open to suggestions

Colors

Designer to choose colors to be used in the design.

Requirements
Must have
• Three most important things: Trustworthy, Authentic, Simple
• Please use colors form logo and grays
• We like: www.hollowmere.com
• https://www.quillfenbrook.com/
• We need Agent Look up tool on home page similar to what is shown on example sites.
• Design:
• Home Page - Open to Ideas
• Insurance (Products) Landing Page - Info similar to: https://www.quillfenbrook.com/insurance/
• Agents Page - https://www.quillfenbrook.com/agents/
• Claims Page - Information similar to: https://www.quillfenbrook.com/claims-center/
• Site Navigation:
• Home
• Insurance
• Claims
• Agents
• About Us
• Contact Us
Nice to have
• Elegant, minimal and clean design that reflects trust and authenticity.
Should not have
• Slider or rotating images - prefer flat design. Not over powering design.

```html
<!DOCTYPE html>
<html lang="en">
<head>
<meta charset="utf-8">
<title>Hearthwell Insurance Co.</title>
<link rel="stylesheet" href="https://fonts.googleapis.com/css2?family=Open+Sans:wght@400;600;700&family=Raleway:wght@400;500;600&display=swap">
<style>
:root{
  --navy:#1d3a7a;
  --navy-deep:#15295a;
  --red:#d3202b;
  --ink:#2a2a2a;
  --text:#555;
  --grey-bg:#f3f3f3;
  --line:#cfcfcf;
  --footer:#1f1f1f;
  --white:#fff;
}
*{box-sizing:border-box;margin:0;padding:0}
html,body{width:1200px;height:2903px;overflow:hidden}
body{font-family:"Raleway",sans-serif;color:var(--text);background:var(--white);position:relative}
.head-font{font-family:"Open Sans",sans-serif}
.wrap{width:918px;margin:0 auto;position:relative}
.btn{display:inline-block;font-family:"Open Sans",sans-serif;font-size:13px;font-weight:600;text-transform:uppercase;letter-spacing:.5px;color:var(--white);text-decoration:none;text-align:center}
.btn-red{background:var(--red)}
.btn-navy{background:var(--navy)}
.btn-ghost{border:1px solid var(--white);color:var(--white)}
.btn-white{background:var(--white);color:var(--red)}
input,textarea{font-family:"Raleway",sans-serif}

/* header + hero */
.hero{position:relative;height:548px}
.hero-photo{position:absolute;inset:0;background:linear-gradient(100deg,#8d9aa6 0%,#b6b9b4 30%,#c9a18a 55%,#8e6f5e 80%,#6c7e6a 100%)}
.hero-photo::after{content:"";position:absolute;left:0;right:0;bottom:0;height:140px;background:linear-gradient(transparent,#5f7a4b)}
.site-header{position:absolute;top:0;left:0;right:0;height:86px;background:rgba(255,255,255,.82)}
.site-header .wrap{display:flex;align-items:center;justify-content:space-between;height:86px;padding-left:10px}
.brand{display:flex;align-items:center;gap:12px;font-family:"Open Sans",sans-serif;font-weight:700;font-size:24px;color:var(--navy);letter-spacing:.3px}
.brand-mark{width:26px;height:26px;background:var(--navy)}
.main-nav{display:flex;align-items:center;gap:22px;font-family:"Open Sans",sans-serif;font-size:14px}
.main-nav a{color:var(--ink);text-decoration:none}
.main-nav a.is-active{color:var(--red)}
.main-nav a.nav-quote{background:var(--navy);color:var(--white);padding:7px 9px}
.hero-card{position:absolute;left:141px;top:267px;width:492px;height:145px;background:rgba(255,255,255,.55);border-radius:6px;padding:20px 18px}
.hero-card h1{font-family:"Open Sans",sans-serif;font-weight:600;font-size:25px;line-height:33px;color:#1b1b1b;text-transform:uppercase;letter-spacing:.6px}
.hero-card .btn{position:absolute;left:25px;bottom:-12px;padding:7px 12px}

/* policy circles */
.policies{position:relative;height:168px}
.policy{position:absolute;top:-81px;width:200px;text-align:center}
.policy-ring{width:162px;height:162px;margin:0 auto;border-radius:50%;background:#e6e6e6;display:flex;align-items:center;justify-content:center}
.policy-disc{width:146px;height:146px;border-radius:50%;background:var(--white);display:flex;align-items:center;justify-content:center}
.policy-label{margin-top:18px;font-family:"Open Sans",sans-serif;font-weight:600;font-size:16px;line-height:21px;color:var(--red);text-transform:uppercase}

/* about */
.about{height:344px}
.about .wrap{display:flex;justify-content:space-between}
.about-text{width:616px;padding-top:28px}
.section-title{font-family:"Open Sans",sans-serif;font-weight:400;font-size:26px;color:var(--ink);letter-spacing:.5px}
.title-rule{height:1px;background:var(--line);margin:18px 0 22px;position:relative}
.title-rule::before{content:"";position:absolute;left:0;top:-2px;width:62px;height:4px;background:var(--navy)}
.about-text p{font-size:13px;line-height:23px;color:#444}
.about-text .btn{margin-top:20px;padding:8px 28px}
.quote-box{width:240px;height:283px;background:#f1f1f1;border:1px solid #ddd;margin-top:4px}
.quote-box h2{background:var(--navy);color:var(--white);font-family:"Open Sans",sans-serif;font-weight:600;font-size:20px;text-align:center;padding:5px 0}
.quote-box form{padding:12px 14px}
.quote-box input,.quote-box textarea{display:block;width:100%;height:32px;border:1px solid #d6d6d6;background:#ececec;font-size:11px;padding:0 10px;margin-bottom:6px;color:#888}
.quote-box textarea{height:50px;padding-top:8px;resize:none}
.quote-box .btn{display:block;width:100%;padding:8px 0;border:0;margin-top:6px}

/* audiences */
.audiences{display:flex;height:326px}
.audience{position:relative;flex:1;text-align:center;color:var(--white)}
.audience-photo{position:absolute;inset:0}
.audience--customers .audience-photo{background:linear-gradient(90deg,#1d1d1d,#4a4a4a 45%,#2b2b2b)}
.audience--agents .audience-photo{background:linear-gradient(90deg,#a81620,#d7262f 50%,#b81a24)}
.audience-body{position:relative;padding-top:46px}
.audience h3{font-family:"Open Sans",sans-serif;font-weight:600;font-size:21px;margin:10px 0 14px}
.audience p{width:330px;margin:0 auto;font-size:13px;line-height:23px}
.audience .btn{margin-top:22px;padding:7px 28px}

/* insurance */
.insurance{background:var(--grey-bg);height:628px;padding-top:46px}
.insurance .section-title{text-align:center}
.insurance .title-rule{width:612px;margin:26px auto 0}
.insurance .title-rule::before{left:50%;margin-left:-31px}
.cards{display:flex;margin-top:52px;height:412px}
.card{position:relative;flex:1;overflow:hidden}
.card-photo{position:absolute;inset:0}
.card--home .card-photo{background:linear-gradient(180deg,#e6e7e9,#a49a90 55%,#2a2a2a)}
.card--tenant .card-photo{background:linear-gradient(180deg,#e2c6a9,#b9886a 50%,#6d5447)}
.card--flood .card-photo{background:linear-gradient(180deg,#6f8f4c,#8a4036 50%,#1f1f1f)}
.card-body{position:absolute;left:0;right:0;bottom:0;height:180px;padding:24px 20px 0;text-align:center;color:var(--white);background:linear-gradient(transparent,rgba(0,0,0,.7) 30%)}
.card--tenant .card-body{height:214px;left:0;right:0;background:rgba(36,70,150,.9);padding-top:22px}
.card h3{font-family:"Raleway",sans-serif;font-weight:600;font-size:19px}
.card-rule{width:50px;height:2px;background:var(--red);margin:9px auto 10px}
.card p{font-size:11px;line-height:18px}
.card-actions{display:flex;justify-content:center;gap:12px;margin-top:14px}
.card-actions .btn{padding:7px 0;font-size:12px;width:108px}
.card-actions .btn-navy{width:130px}

/* agent finder */
.agent-finder{background:var(--navy-deep);height:292px;margin-top:58px;text-align:center;color:var(--white);padding-top:50px}
.agent-finder h2{font-family:"Open Sans",sans-serif;font-weight:600;font-size:24px;letter-spacing:.5px}
.agent-finder .rule{width:64px;height:3px;background:var(--white);margin:14px auto 22px}
.agent-finder p{width:620px;margin:0 auto;font-size:13px;line-height:23px}
.finder-form{display:flex;justify-content:center;gap:8px;margin-top:20px}
.finder-form input{width:156px;height:30px;border:0;padding:0 8px;font-size:11px;color:#777}
.finder-form .btn{width:156px;line-height:30px}

/* claim + contact */
.claims{height:312px}
.claims .wrap{display:flex;padding-top:54px}
.claim-panel{width:300px;text-align:center}
.claim-panel h2{font-family:"Open Sans",sans-serif;font-weight:600;font-size:26px;color:var(--navy)}
.claim-panel .claim-big{font-family:"Open Sans",sans-serif;font-weight:700;font-size:50px;color:var(--red);line-height:58px}
.claim-panel p{font-family:"Open Sans",sans-serif;font-size:14px;line-height:24px;color:var(--navy);margin-top:6px}
.claim-panel .btn{margin-top:26px;padding:8px 28px}
.divider{width:1px;height:200px;background:var(--line);margin:0 40px 0 4px}
.contact-form{width:528px}
.contact-form h2{font-family:"Open Sans",sans-serif;font-weight:400;font-size:25px;color:var(--ink)}
.contact-form .title-rule{margin:12px 0 12px}
.contact-form small{font-size:11px;color:#444}
.form-grid{display:grid;grid-template-columns:1fr 1fr;gap:12px 12px;margin-top:12px}
.form-grid input{height:32px;border:1px solid #ccc;padding:0 10px;font-size:11px;color:#777}
.contact-form .btn{margin-top:16px;padding:7px 14px;border:0}

/* footer */
.site-footer{background:var(--footer);height:250px;color:#ccc}
.site-footer .wrap{display:flex;padding-top:40px}
.foot-col h4{font-family:"Raleway",sans-serif;font-weight:500;font-size:16px;color:var(--white)}
.foot-col .rule{height:1px;background:#444;margin:10px 0 14px}
.quick-links{width:124px;margin-left:18px}
.quick-links ul{list-style:none;font-size:11px;line-height:22px}
.quick-links li::before{content:"›";margin-right:6px;color:#888}
.quick-links li.is-active{color:#3c4a7a}
.contact-detail{width:196px;margin-left:36px}
.contact-detail strong{display:block;font-size:12px;font-weight:600;color:var(--white)}
.contact-detail p{font-size:11px;line-height:18px;margin-top:4px}
.contact-line{display:flex;align-items:center;gap:10px;margin-top:18px;font-size:13px}
.contact-line.small{font-size:11px;margin-top:12px}
.newsletter{width:214px;margin-left:90px}
.newsletter p{font-size:11px;line-height:20px}
.newsletter input{display:block;width:172px;height:30px;background:#4a4a4a;border:0;color:#ddd;font-size:11px;padding:0 8px;margin-top:12px}
.newsletter .btn{margin-top:10px;padding:6px 16px;text-transform:none;font-family:"Raleway",sans-serif;font-size:12px}
.footer-name{margin-left:auto;margin-right:14px;margin-top:30px;width:136px;font-family:"Open Sans",sans-serif;font-weight:700;font-size:20px;line-height:26px;color:#cfcfcf;text-align:center}
.bottom-bar{background:var(--navy);height:35px}
.bottom-bar .wrap{display:flex;justify-content:space-between;align-items:center;height:35px;font-family:"Open Sans",sans-serif;font-weight:600;font-size:12px;color:var(--white)}
.social{display:flex;gap:6px}
.social span{width:20px;height:20px;border:1px solid var(--white);background:#2a55a3}
</style>
</head>
<body>

<section class="hero">
  <div class="hero-photo" role="img" aria-label="Smiling family of four in front of a suburban house"></div>
  <header class="site-header">
    <div class="wrap">
      <div class="brand"><span class="brand-mark"></span>Hearthwell Insurance Co.</div>
      <nav class="main-nav">
        <a class="is-active" href="#">Home</a>
        <a href="#">About Us</a>
        <a href="#">Insurance</a>
        <a href="#">Agents</a>
        <a href="#">Claims</a>
        <a href="#">Contact Us</a>
        <a class="nav-quote" href="#">Get a quote</a>
      </nav>
    </div>
  </header>
  <div class="hero-card">
    <h1>Get homeowners insurance policy / tenants policy/ flood insurance in USA</h1>
    <a class="btn btn-red" href="#">Read more</a>
  </div>
</section>

<section class="policies">
  <div class="policy" style="left:213px">
    <div class="policy-ring"><div class="policy-disc">
      <svg width="56" height="56" viewBox="0 0 56 56" fill="#d3202b"><path d="M28 6 8 22h6v14h28V22h6z"/><text x="28" y="32" font-size="14" font-family="Open Sans" font-weight="700" fill="#fff" text-anchor="middle">%</text><path d="M6 42h14l10 4 14-6 4 3-18 9-24-2z"/></svg>
    </div></div>
    <div class="policy-label">Homeowners<br>policy</div>
  </div>
  <div class="policy" style="left:500px">
    <div class="policy-ring"><div class="policy-disc">
      <svg width="56" height="56" viewBox="0 0 56 56" fill="#d3202b"><path d="M28 4 4 24h6v26h36V24h6z"/><circle cx="22" cy="26" r="4" fill="#fff"/><circle cx="34" cy="26" r="4" fill="#fff"/><rect x="18" y="31" width="8" height="15" fill="#fff"/><rect x="30" y="31" width="8" height="15" fill="#fff"/></svg>
    </div></div>
    <div class="policy-label" style="margin-top:28px">Tenants policy</div>
  </div>
  <div class="policy" style="left:780px">
    <div class="policy-ring"><div class="policy-disc">
      <svg width="60" height="56" viewBox="0 0 60 56" fill="#d3202b"><path d="M30 6 10 22h5v14h30V22h5z"/><rect x="25" y="26" width="10" height="10" fill="#fff"/><path d="M6 42q6-5 12 0t12 0 12 0 12 0v4q-6-5-12 0t-12 0-12 0-12 0z"/><path d="M6 50q6-5 12 0t12 0 12 0 12 0v4q-6-5-12 0t-12 0-12 0-12 0z"/></svg>
    </div></div>
    <div class="policy-label" style="margin-top:28px">Flood insurance</div>
  </div>
</section>

<section class="about">
  <div class="wrap">
    <div class="about-text">
      <h2 class="section-title">ABOUT US</h2>
      <div class="title-rule"></div>
      <p>Lorem ipsum dolor sit amet, consectetuer adipiscing elit, sed diam nonummy nibh euismod tincidunt ut laoreet dolore magna aliquam erat volutpat. Ut wisi enim ad minim veniam, quis nostrud exerci tation ullamcorper suscipit lobortis nisl ut aliquip ex ea commodo consequat. Duis autem vel eum iriure dolor in hendrerit in vulputate velit esse molestie consequat, vel illum dolore eu feugiat nulla facilisis at vero eros et accumsan et iusto odio dignissim qui blandit praesent luptatum zzril delenit augue duis dolore te feugait nulla facilisi.</p>
      <a class="btn btn-navy" href="#">Read more</a>
    </div>
    <aside class="quote-box">
      <h2>Get A Quote</h2>
      <form>
        <input type="text" placeholder="Name">
        <input type="text" placeholder="Email">
        <input type="text" placeholder="Subject">
        <textarea placeholder="Message"></textarea>
        <button class="btn btn-navy" type="button">Submit</button>
      </form>
    </aside>
  </div>
</section>

<section class="audiences">
  <div class="audience audience--customers">
    <div class="audience-photo" role="img" aria-label="Customers shaking hands with an advisor at a desk"></div>
    <div class="audience-body">
      <svg width="70" height="44" viewBox="0 0 70 44" fill="#fff"><path d="M2 10h12l6 18H8z"/><path d="M68 10H56l-6 18h12z"/><path d="M18 12h12l8 4 8-4h8l4 14-12 10-6-2-4 2-16-10z"/></svg>
      <h3>Customers</h3>
      <p>Lorem ipsum dolor sit amet, consectetuer adipiscing elit, sed diam nonummy nibh euismod tincidunt ut laoreet dolore magna aliquam erat volutpat</p>
      <a class="btn btn-ghost" href="#">Read more</a>
    </div>
  </div>
  <div class="audience audience--agents">
    <div class="audience-photo" role="img" aria-label="Insurance agent working at a laptop"></div>
    <div class="audience-body" style="padding-top:36px">
      <svg width="68" height="68" viewBox="0 0 68 68"><circle cx="34" cy="34" r="33" fill="#fff"/><circle cx="34" cy="24" r="7" fill="#d3202b"/><path d="M22 46c0-9 5-14 12-14s12 5 12 14z" fill="#d3202b"/><circle cx="18" cy="30" r="5" fill="#d3202b"/><circle cx="50" cy="30" r="5" fill="#d3202b"/><path d="M10 48c0-7 4-11 8-11s6 2 6 4l-4 7zM58 48c0-7-4-11-8-11s-6 2-6 4l4 7z" fill="#d3202b"/></svg>
      <h3>Agents</h3>
      <p>Lorem ipsum dolor sit amet, consectetuer adipiscing elit, sed diam nonummy nibh euismod tincidunt ut laoreet dolore magna aliquam erat volutpat</p>
      <a class="btn btn-ghost" href="#">Read more</a>
    </div>
  </div>
</section>

<section class="insurance">
  <h2 class="section-title">INSURANCE</h2>
  <div class="title-rule"></div>
  <div class="wrap cards">
    <article class="card card--home">
      <div class="card-photo" role="img" aria-label="Couple looking around a bright new home"></div>
      <div class="card-body">
        <h3>Homeowner Policy</h3>
        <div class="card-rule"></div>
        <p>Lorem ipsum dolor sit amet, consectetuer adipiscing elit, sed diam nonummy nibh euismod tincidunt ut laoreet dolore magna aliquam erat volutpat.</p>
        <div class="card-actions"><a class="btn btn-red" href="#">Quote →</a><a class="btn btn-navy" href="#">Read more →</a></div>
      </div>
    </article>
    <article class="card card--tenant">
      <div class="card-photo" role="img" aria-label="Young couple reviewing documents together"></div>
      <div class="card-body">
        <h3>Tenant Policy</h3>
        <div class="card-rule"></div>
        <p>Lorem ipsum dolor sit amet, consectetuer adipiscing elit, sed diam nonummy nibh euismod tincidunt ut laoreet dolore magna aliquam erat volutpat.</p>
        <div class="card-actions"><a class="btn btn-red" href="#">Quote →</a><a class="btn btn-white" href="#">Read more →</a></div>
      </div>
    </article>
    <article class="card card--flood">
      <div class="card-photo" role="img" aria-label="Red wooden house tilted by flood water"></div>
      <div class="card-body">
        <h3>Flood Policy</h3>
        <div class="card-rule"></div>
        <p>Lorem ipsum dolor sit amet, consectetuer adipiscing elit, sed diam nonummy nibh euismod tincidunt ut laoreet dolore magna aliquam erat volutpat.</p>
        <div class="card-actions"><a class="btn btn-red" href="#">Quote →</a><a class="btn btn-navy" href="#">Read more →</a></div>
      </div>
    </article>
  </div>
</section>

<section class="agent-finder" style="margin-top:0">
  <h2>FIND AN AGENT</h2>
  <div class="rule"></div>
  <p>Lorem ipsum dolor sit amet, consectetuer adipiscing elit, sed diam nonummy nibh euismod tincidunt ut laoreet dolore magna aliquam erat volutpat. Ut wisi enim ad minim veniam, quis nostrud exerci tation ullamcorper suscipit lobortis nisl ut aliquip ex ea commodo consequat.</p>
  <form class="finder-form">
    <input type="text" placeholder="Search...">
    <a class="btn btn-red" href="#">Find an agent</a>
  </form>
</section>

<section class="claims">
  <div class="wrap">
    <div class="claim-panel">
      <h2>Report And Check</h2>
      <div class="claim-big">A Claim</div>
      <p>Login To Report A Claim Or<br>Check Your Claim Status.</p>
      <a class="btn btn-red" href="#">Login</a>
    </div>
    <div class="divider"></div>
    <div class="contact-form">
      <h2>CONTACT FORM</h2>
      <div class="title-rule"></div>
      <small>Please fill up bellow form</small>
      <div class="form-grid">
        <input type="text" placeholder="Name">
        <input type="text" placeholder="Email">
        <input type="text" placeholder="Phone">
        <input type="text" placeholder="Message">
      </div>
      <button class="btn btn-red" type="button">Submit</button>
    </div>
  </div>
</section>

<footer class="site-footer">
  <div class="wrap">
    <div class="foot-col quick-links">
      <h4>Quick Links</h4>
      <div class="rule"></div>
      <ul>
        <li class="is-active">Home</li>
        <li>About Us</li>
        <li>Insurance</li>
        <li>Agents</li>
        <li>Claims</li>
        <li>Contact Us</li>
      </ul>
    </div>
    <div class="foot-col contact-detail">
      <h4>Contact Detail</h4>
      <div class="rule"></div>
      <strong>Hearthwell Insurance</strong>
      <p>Lorem ipsum dolor sit amet, consectetur adipiscing elit, sed do eiusmod</p>
      <div class="contact-line">
        <svg width="14" height="14" viewBox="0 0 24 24" fill="#3f6bd1"><path d="M6.6 10.8a15 15 0 0 0 6.6 6.6l2.2-2.2a1 1 0 0 1 1-.25 11.4 11.4 0 0 0 3.6.57 1 1 0 0 1 1 1V20a1 1 0 0 1-1 1A17 17 0 0 1 3 4a1 1 0 0 1 1-1h3.5a1 1 0 0 1 1 1c0 1.25.2 2.45.57 3.57a1 1 0 0 1-.25 1z"/></svg>
        555.010.2480
      </div>
      <div class="contact-line small">
        <svg width="14" height="11" viewBox="0 0 24 18" fill="#3f6bd1"><path d="M0 0h24v18H0z"/><path d="M1 1l11 8 11-8" stroke="#1f1f1f" stroke-width="2" fill="none"/></svg>
        info@hearthwell.com
      </div>
    </div>
    <div class="foot-col newsletter">
      <h4>Join Our Newsletter</h4>
      <div class="rule"></div>
      <p>Subscribe to our Newsletter to get the latest scoop right to your inbox</p>
      <input type="text" placeholder="Enter Your Email">
      <a class="btn btn-red" href="#">Subscribe</a>
    </div>
    <div class="footer-name">Hearthwell Insurance Co.</div>
  </div>
</footer>
<div class="bottom-bar">
  <div class="wrap">
    <span>© 2018 Hearthwellinsurance.com. All Rights Reserved.</span>
    <div class="social" aria-label="Social links"><span></span><span></span><span></span></div>
  </div>
</div>

</body>
</html>
```